Wine producer needing new wine lables

HI
i require a new wine lable design
must be front and back lable

looking to use only colors of black and gold (shiny gold)

Please look at the image i have uploaded for your reference.

i want the basic concept like that image i have supplied
for the front label please use this information

the bottling location is - South Austtralia
Wine name - Oakmere bend
Milesime - 2016
under millesime - Cabernet Sauvignon
appellation - Wine of Australia

Sorry I forgot to mention the label is to be 13.5cm high by10.5 cm wide

Target Market(s)

Chinese wine buyers

Logo Text

Corvanne Estate Wines, 2016 cabernet sauvignon, Wine of australia

Logo styles of interest
Emblem Logo
Font styles to use
Decorative

Requirements
Must have
• Must have informtion i have supplied,
• must be black and gold,
• maybe black lable with all imagery and information in gold
• must have a palace/royal building in centre
• Lable must be put on a wine bottle
• Sorry I forgot to mention the label is to be 13.5cm high by10.5 cm wide
Nice to have
• the "palace in the middle" must be original design
• i want the "Palace/building' to look like a royal family lives their
Should not have
• bright colors
• animlas
• please put the label on a wine bottle so we can see properly, will not ecept images that resemble business cards.

```html
<!DOCTYPE html>
<html lang="en">
<head>
<meta charset="utf-8">
<title>Oakmere Bend – 2016 Cabernet Sauvignon Label</title>
<link rel="stylesheet" href="https://fonts.googleapis.com/css2?family=Cinzel:wght@400;600&family=Josefin+Sans:wght@400&display=swap">
<style>
  :root {
    --stage: #3a3836;
    --label-black: #000000;
    --gold: #d9b23a;
    --gold-light: #ecd27a;
    --gold-deep: #9c7a1e;
  }
  html, body {
    margin: 0;
    padding: 0;
    width: 1200px;
    height: 600px;
    overflow: hidden;
    background: var(--stage);
  }
  .canvas {
    position: relative;
    width: 1200px;
    height: 600px;
    display: flex;
    align-items: center;
    justify-content: center;
  }
  .label {
    display: block;
    width: 768px;
    height: 600px;
  }
  .label-ground { fill: var(--label-black); }
  .frame-line {
    fill: none;
    stroke: var(--gold);
    stroke-width: 3;
  }
  .frame-corner { fill: var(--gold); }
  .region {
    font-family: "Josefin Sans", sans-serif;
    font-size: 27px;
    letter-spacing: 5px;
    fill: var(--gold);
  }
  .appellation {
    font-family: "Josefin Sans", sans-serif;
    font-size: 25px;
    letter-spacing: 6px;
    fill: var(--gold);
  }
  .wine-name {
    font-family: "Cinzel", serif;
    font-weight: 400;
    font-size: 84px;
    fill: var(--gold);
    letter-spacing: 1px;
  }
  .vintage {
    font-family: "Cinzel", serif;
    font-size: 40px;
    fill: var(--gold);
    letter-spacing: 2px;
  }
  .variety {
    font-family: "Cinzel", serif;
    font-size: 50px;
    fill: var(--gold);
  }
</style>
</head>
<body>
<main class="canvas">
  <svg class="label" viewBox="0 0 960 750" xmlns="http://www.w3.org/2000/svg" aria-label="Oakmere Bend 2016 Cabernet Sauvignon front label">
    <defs>
      <linearGradient id="palace-tone" x1="0" y1="0" x2="0" y2="1">
        <stop offset="0" stop-color="var(--gold-light)"/>
        <stop offset="1" stop-color="var(--gold-deep)"/>
      </linearGradient>
      <path id="name-arc" d="M 105 340 Q 480 100 855 340"/>
      <path id="variety-arc" d="M 175 480 Q 480 760 795 480"/>
    </defs>

    <rect class="label-ground" x="0" y="0" width="960" height="750"/>

    <g class="frame">
      <rect class="frame-line" x="16" y="16" width="928" height="718"/>
      <path class="frame-line" d="M 100 40 H 860 L 920 100 V 650 L 860 710 H 100 L 40 650 V 100 Z"/>
      <path class="frame-line" d="M 16 80 L 80 16 M 880 16 L 944 80 M 944 670 L 880 734 M 80 734 L 16 670"/>
      <path class="frame-corner" d="M 22 22 H 62 L 22 62 Z M 938 22 V 62 L 898 22 Z M 938 728 H 898 L 938 688 Z M 22 728 V 688 L 62 728 Z"/>
    </g>

    <text class="region" x="480" y="98" text-anchor="middle">SOUTH AUSTRALIA</text>

    <text class="wine-name">
      <textPath href="#name-arc" startOffset="50%" text-anchor="middle">OAKMERE BEND</textPath>
    </text>

    <rect class="palace-emblem" x="275" y="290" width="420" height="188" fill="url(#palace-tone)" role="img" aria-label="Gold line illustration of a grand royal palace with mansard roof, rooftop statues and rows of tall windows"/>

    <text class="vintage" x="480" y="558" text-anchor="middle">2016</text>

    <text class="variety">
      <textPath href="#variety-arc" startOffset="50%" text-anchor="middle">CABERNET SAUVIGNON</textPath>
    </text>

    <text class="appellation" x="480" y="693" text-anchor="middle">WINE OF AUSTRALIA</text>
  </svg>
</main>
</body>
</html>
```